Building company buisness cards

We are looking for a sharp modern new look for our business cards.We are a New Zealand based company that specialises in house and land packages.We have attached a photo of the current logo and would like to see if it can be improved somehow if needed.We are open to any colours but we have chosen Black and White at this stage. Feel free to change the font and make the logo smarter looking.Play with the colours and see what looks best.We want a card that looks so good know one will want to throw it away!

Target Market(s)

Building profesonals, home buyers

Industry/Entity Type

Building

Contact Information for Business Card

Garrick Tenwood
0275390628
garrickt@hartvale.co.nz

Font styles to use
Serif
Sans Serif

Colors

Designer to choose colors to be used in the design.

Requirements
Must have
• Just the logo on one side and details on the other
• Clean simple looking card
Nice to have
• Round corners and detail like raised or spot UV
• Something that stands out
Should not have
• To title needed, Director etc

```html
<!DOCTYPE html>
<html lang="en">
<head>
<meta charset="utf-8">
<title>Hartvale Business Card</title>
<link rel="stylesheet" href="https://fonts.googleapis.com/css2?family=Roboto:wght@300;400;700&display=swap">
<style>
  :root {
    --backdrop: #e3e3e3;
    --paper: #ffffff;
    --ink: #0b0c10;
    --ink-soft: #454545;
    --reverse: #ffffff;
  }
  * { margin: 0; padding: 0; box-sizing: border-box; }
  html, body {
    width: 1125px;
    height: 1200px;
    overflow: hidden;
    background: var(--backdrop);
    font-family: "Roboto", Arial, sans-serif;
  }
  .card {
    position: absolute;
    left: 166px;
    width: 800px;
    height: 456px;
    border-radius: 24px;
    overflow: hidden;
  }
  .card--front { top: 104px; background: var(--paper); }
  .card--back { top: 620px; background: var(--ink); }

  .front-band {
    position: absolute;
    left: 672px;
    top: 60px;
    width: 128px;
    height: 98px;
    background: var(--ink);
  }
  .front-mark {
    position: absolute;
    left: 690px;
    top: 78px;
    width: 62px;
    height: 62px;
    border-radius: 50%;
    background: var(--paper);
  }
  .front-name {
    position: absolute;
    right: 144px;
    top: 64px;
    font-size: 70px;
    font-weight: 700;
    line-height: 86px;
    color: var(--ink);
  }

  .holder {
    position: absolute;
    left: 54px;
    top: 276px;
    font-size: 28px;
    font-weight: 700;
    color: var(--ink);
  }
  .contact-list {
    position: absolute;
    left: 54px;
    top: 330px;
    list-style: none;
  }
  .contact-list li {
    display: flex;
    align-items: center;
    height: 25.5px;
    font-size: 19px;
    color: var(--ink-soft);
  }
  .contact-list svg {
    width: 17px;
    height: 17px;
    margin-right: 13px;
    fill: var(--ink);
  }

  .back-logo {
    position: absolute;
    left: 0;
    right: 0;
    top: 172px;
    display: flex;
    justify-content: center;
    align-items: center;
    gap: 24px;
  }
  .back-name {
    font-size: 84px;
    font-weight: 700;
    line-height: 110px;
    color: var(--reverse);
  }
  .back-mark {
    width: 96px;
    height: 96px;
    border-radius: 50%;
    background: var(--reverse);
  }
  .back-web {
    position: absolute;
    left: 0;
    right: 0;
    top: 380px;
    text-align: center;
    font-size: 17px;
    font-weight: 300;
    letter-spacing: 4px;
    color: var(--reverse);
  }
</style>
</head>
<body>
  <section class="card card--front">
    <div class="front-band"></div>
    <div class="front-name">Hartvale</div>
    <div class="front-mark"></div>

    <h1 class="holder">Garrick Tenwood</h1>
    <ul class="contact-list">
      <li>
        <svg viewBox="0 0 24 24" aria-hidden="true"><path d="M6.6 10.8a15.1 15.1 0 0 0 6.6 6.6l2.2-2.2a1 1 0 0 1 1-.25 11.4 11.4 0 0 0 3.6.57 1 1 0 0 1 1 1V20a1 1 0 0 1-1 1A17 17 0 0 1 3 4a1 1 0 0 1 1-1h3.5a1 1 0 0 1 1 1c0 1.25.2 2.45.57 3.57a1 1 0 0 1-.25 1z"/></svg>
        0275390628
      </li>
      <li>
        <svg viewBox="0 0 24 24" aria-hidden="true"><path d="M2 5h20v14H2z M4 7v.5l8 5 8-5V7l-8 5z" fill-rule="evenodd"/></svg>
        garrickt@hartvale.co.nz
      </li>
      <li>
        <svg viewBox="0 0 24 24" aria-hidden="true"><circle cx="12" cy="12" r="10"/><path d="M7 6c2 1 3 3 2 5s1 3 3 3 1 4 0 6M15 4c-1 2 0 3 2 3s3 2 2 4" stroke="#fff" stroke-width="2" fill="none"/></svg>
        www.hartvale.co.nz
      </li>
    </ul>
  </section>

  <section class="card card--back">
    <div class="back-logo">
      <div class="back-name">Hartvale</div>
      <div class="back-mark"></div>
    </div>
    <p class="back-web">www.hartvale.co.nz</p>
  </section>
</body>
</html>
```